Accountability Project Graphics

I want to create 10 social media graphics (new Instagram size 4:5 (1080 x 1350 pixels) focusing on our Quilvo Accountability App, using any of the 3 pictures attached. Use the attached pics only, NO RANDOM STOCK PHOTOGRAPHY. For the color scheme, use the landing page colors/fonts (attached).
You can add any of the 3 photos attached but I mainly need BOLD text that includes these headlines and sub-headlines on them.
Please NOTE for all the headlines below, also add this sub-headline on each graphic:
Stay Consistent with RT in Your Pocket!
Here are the headlines:
• Stop Starting Over Every Monday
• You don't need more willpower. You need more support
• Built for women who are tired of doing this alone
• When Motivation Fades, RT Checks In
• The Support System You've Been Missing
• Support When Motivation Disappears
• What if RT Checked in Every Day?
• The Missing Piece Isn't Another Diet
• Eat the food you love. Stay accountable every day.
• One Bad Meal Doesn't Mean You Failed
women over 40 trying to lose weight

```html
<!DOCTYPE html>
<html lang="en">
<head>
<meta charset="utf-8">
<title>Quilvo Accountability Graphics</title>
<link href="https://fonts.googleapis.com/css2?family=Fraunces:opsz,wght@9..144,700&family=Open+Sans:wght@400;600&display=swap" rel="stylesheet">
<style>
:root{
  --board:#2e1a3f;
  --card:#fcf1f2;
  --blush:#f7dce3;
  --ink:#2b1838;
  --rose:#c8527a;
  --plum:#5e2550;
  --white:#ffffff;
  --photo-a:#c9a3a8;
  --photo-b:#3a2a44;
  --photo-mid:#6f566c;
}
*{margin:0;padding:0;box-sizing:border-box}
html,body{width:1200px;height:996px;overflow:hidden;background:var(--board)}
.board{position:relative;width:1200px;height:996px}
.post{position:absolute;width:374px;height:468px;background:var(--card);overflow:hidden;font-family:"Open Sans",sans-serif;color:var(--ink)}
.post--1{left:19px;top:21px}
.post--2{left:413px;top:21px}
.post--3{left:807px;top:21px}
.post--4{left:19px;top:507px}
.post--5{left:413px;top:507px}
.glow{position:absolute;border-radius:50%;background:var(--blush)}
.photo{position:absolute;background:linear-gradient(180deg,var(--photo-a),var(--photo-b))}
.headline{position:absolute;font-family:"Fraunces",serif;font-weight:700;letter-spacing:-0.5px;white-space:nowrap}
.headline .accent{color:var(--rose)}
.sub{position:absolute;font-size:16px;line-height:19px;white-space:nowrap}
.bubble{position:absolute;width:158px;height:52px;background:var(--white);border-radius:8px;padding:9px 0 0 17px;font-size:12px;line-height:16px;white-space:nowrap}
.bubble b{font-weight:600}
.bubble .who{color:var(--rose);font-weight:600}
.bubble .line2{padding-left:17px}
.call{position:absolute;width:186px;height:51px;background:var(--plum);border-radius:9px;display:flex;align-items:center;gap:10px;padding-left:16px;color:var(--white);font-size:13px;white-space:nowrap}
</style>
</head>
<body>
<div class="board">

  <section class="post post--1">
    <div class="glow" style="left:208px;top:30px;width:300px;height:300px"></div>
    <div class="glow" style="left:170px;top:250px;width:280px;height:280px;opacity:.6"></div>
    <div class="photo" role="img" aria-label="Smiling coach in a black mesh top and jeans, hand on hip" style="left:198px;top:22px;width:176px;height:446px;border-radius:80px 80px 0 0"></div>
    <h1 class="headline" style="left:19px;top:30px;font-size:41px;line-height:41px">Stop<br>Starting<br>Over<br><span class="accent">Every<br>Monday</span></h1>
    <p class="sub" style="left:17px;top:258px">Stay Consistent with<br>RT in Your Pocket!</p>
    <div class="bubble" style="left:18px;top:313px"><span class="who">RT:</span> <b>You good, sis?</b><br><span class="line2">You've got this.</span></div>
    <div class="call" style="left:18px;top:377px">
      <svg width="22" height="22" viewBox="0 0 24 24" fill="none"><path d="M6.6 3.5l2.6 3.2-1.7 2.2a12 12 0 006.6 6.6l2.2-1.7 3.2 2.6-1.6 3.1C11 19.5 4.5 13 4 5.1z" fill="#d8678e"/><path d="M14 4a6 6 0 016 6M14 7.5a2.5 2.5 0 012.5 2.5" stroke="#d8678e" stroke-width="1.8" stroke-linecap="round"/></svg>
      Weekly calls from RT
    </div>
  </section>

  <section class="post post--2">
    <div class="glow" style="left:160px;top:-40px;width:300px;height:300px"></div>
    <div class="glow" style="left:230px;top:260px;width:260px;height:260px;opacity:.7"></div>
    <div class="photo" role="img" aria-label="Two women hugging and laughing" style="left:57px;top:200px;width:240px;height:268px;border-radius:110px 110px 0 0"></div>
    <h2 class="headline" style="left:19px;top:32px;font-size:35px;line-height:36px">You don't need<br>more willpower.<br><span class="accent">You need more<br>support.</span></h2>
    <p class="sub" style="left:205px;top:163px">Stay Consistent with<br>RT in Your Pocket!</p>
  </section>

  <section class="post post--3">
    <div class="glow" style="left:40px;top:148px;width:330px;height:330px"></div>
    <div class="photo" role="img" aria-label="Coach with her arm around a laughing client, both in denim" style="left:29px;top:166px;width:337px;height:302px;border-radius:120px 120px 0 0"></div>
    <h2 class="headline" style="left:19px;top:32px;font-size:33px;line-height:38px">When Motivation<br>Fades, <span class="accent">RT Checks In</span></h2>
    <p class="sub" style="left:19px;top:120px">Stay Consistent with RT in Your Pocket!</p>
    <div class="bubble" style="left:158px;top:158px;padding-top:17px"><span class="who">RT:</span> <b>You good, sis?</b></div>
  </section>

  <section class="post post--4">
    <div class="glow" style="left:215px;top:30px;width:290px;height:290px"></div>
    <div class="glow" style="left:180px;top:260px;width:260px;height:260px;opacity:.6"></div>
    <div class="photo" role="img" aria-label="Smiling coach in a black mesh top, hand on hip" style="left:223px;top:154px;width:151px;height:314px;border-radius:70px 70px 0 0"></div>
    <h2 class="headline" style="left:19px;top:56px;font-size:40px;line-height:42px">What if<br>RT Checked in<br><span class="accent">Every Day?</span></h2>
    <p class="sub" style="left:22px;top:206px">Stay Consistent with<br>RT in Your Pocket!</p>
    <div class="bubble" style="left:18px;top:271px"><span class="who">RT:</span> <b>You good, sis?</b><br><span class="line2">You've got this.</span></div>
    <div class="call" style="left:18px;top:335px">
      <svg width="22" height="22" viewBox="0 0 24 24" fill="none"><path d="M6.6 3.5l2.6 3.2-1.7 2.2a12 12 0 006.6 6.6l2.2-1.7 3.2 2.6-1.6 3.1C11 19.5 4.5 13 4 5.1z" fill="#d8678e"/><path d="M14 4a6 6 0 016 6M14 7.5a2.5 2.5 0 012.5 2.5" stroke="#d8678e" stroke-width="1.8" stroke-linecap="round"/></svg>
      Weekly calls from RT
    </div>
  </section>

  <section class="post post--5">
    <div class="glow" style="left:150px;top:-30px;width:280px;height:280px"></div>
    <div class="photo" role="img" aria-label="Coach hugging a laughing client, both in denim" style="left:57px;top:34px;width:263px;height:263px;border-radius:110px 110px 0 0;background:linear-gradient(180deg,var(--photo-a),var(--photo-mid) 55%,var(--card))"></div>
    <div class="bubble" style="left:166px;top:27px;padding-top:17px"><span class="who">RT:</span> <b>You good, sis?</b></div>
    <h2 class="headline" style="left:0;width:374px;top:266px;font-size:37px;line-height:39px;text-align:center">One Bad Meal<br>Doesn't Mean<br><span class="accent">You Failed</span></h2>
    <p class="sub" style="left:0;width:374px;top:405px;text-align:center">Stay Consistent with RT in Your Pocket!</p>
  </section>

</div>
</body>
</html>
```